Creation of brand identity and website "Tandem K"

I am currently seeking an brand, identity and web design for a new project called Tandem K. This is a brand new concept from scratch and you have free-reign on the whole design process, taking into account my preference below.

Must include the name "Tandem K", or "Tandem K: Or the year I woke Up". Kudos is this forms part of the brands logo

Design that can be easily scaled to potentially include: a blog, timeline and vlogs.

Minimal but effective use of colour (however any colours and combinations permitted

Use of icons/graphics over text wherever possible

Minimal use of frames and borders

I appreciate this is a fairly wide scope so please contact me on marblefinch@postwillow.com with any questions or more information on what the project is.

Target Market(s)

Male and Female 20-40
Blog readers
Selfhelp

Industry/Entity Type

Seeking

Number of Pages Required

1 page

Font styles to use
Serif
Sans Serif

Requirements
Must have
• It is in effect a blog design, so about me section, recent blog / archived posts, reader comments / Q and A section.
• A coded design would be appreciated to make my life easier however I have left the design as uncoded as getting the right design matters more to me and I want to keep the project open to as many designers as possible
Nice to have
• See project description for other details and please ask if you need anything else :)
Should not have
• Mustn't be cluttered or feel fussy
• Promote icons over text
• Frames / multiple borders

```html
<!DOCTYPE html>
<html lang="en">
<head>
<meta charset="utf-8">
<title>Tandem K</title>
<link rel="stylesheet" href="https://fonts.googleapis.com/css2?family=Lato:wght@400;700;900&display=swap">
<style>
:root{
  --orange:#f7a21b;
  --ink:#222;
  --text:#777;
  --muted:#999;
  --line:#e3e3e3;
  --panel:#595959;
  --panel-dark:#4a4a4a;
  --soft:#f2f2f2;
  --white:#fff;
}
*{box-sizing:border-box;margin:0;padding:0}
html,body{width:1200px;height:2786px;overflow:hidden;background:var(--white);font-family:"Lato",Arial,sans-serif;color:var(--ink)}
.page{position:relative;width:1200px;height:2786px}
.topline{position:absolute;top:0;left:0;width:1200px;height:4px;background:#333}

/* header */
.site-header{position:absolute;top:4px;left:0;width:1200px;height:62px}
.brand{position:absolute;left:100px;top:12px;font-size:27px;font-weight:700;color:#333;padding-bottom:6px;border-bottom:3px solid var(--orange);width:290px}
.main-nav{position:absolute;top:28px;left:0;width:1200px;font-size:16px;color:#222}
.main-nav a{position:absolute;color:inherit;text-decoration:none;text-transform:uppercase;white-space:nowrap}
.main-nav a.active{color:var(--orange);padding-bottom:6px;border-bottom:2px solid var(--orange)}

/* hero */
.hero{position:absolute;top:66px;left:0;width:1200px;height:428px;background:linear-gradient(100deg,#3b2a1c 0%,#6e5236 35%,#8a6d4b 55%,#4a3624 75%,#2a1d14 100%)}
.about-card{position:absolute;left:102px;top:40px;width:316px;height:316px;border-radius:50%;background:#ececec;overflow:hidden;box-shadow:0 4px 14px rgba(0,0,0,.35);text-align:center}
.about-card h1{margin-top:64px;font-size:33px;font-weight:900;letter-spacing:.5px;color:#111}
.about-card p{margin:18px auto 0;width:210px;font-size:13px;line-height:19px;color:#222}
.about-card .more{position:absolute;left:0;bottom:0;width:100%;height:34px;background:var(--orange);color:#fff;font-size:26px;font-weight:700;line-height:32px}

/* posts */
.posts{position:absolute;left:100px;top:530px;width:630px}
.post{height:286px;padding-top:0;border-bottom:2px solid var(--line)}
.post.first{height:436px}
.post.last{border-bottom:none;height:260px}
.post h2{font-size:24px;font-weight:400;color:#333;padding-top:0;line-height:30px;margin-top:6px}
.post .post-sub{font-size:12.5px;font-weight:700;color:#222;margin-top:4px}
.post-body{display:flex;justify-content:space-between;margin-top:12px}
.post-body p{width:453px;font-size:12.5px;line-height:18.6px;color:var(--text)}
.post-body p a{color:var(--orange);text-decoration:underline;font-size:11.5px}
.post-photo{width:138px;height:121px;background:linear-gradient(160deg,#c9c3b8,#7d766d)}
.post-meta{display:flex;margin-top:22px;font-size:11.5px;color:#555}
.post-meta span{display:flex;align-items:center;gap:8px}
.post-meta span:nth-child(1){width:123px}
.post-meta span:nth-child(2){width:160px}
.post-meta span:nth-child(3){width:102px}
.post-meta svg{width:14px;height:14px;fill:var(--orange)}

.comments{margin-top:12px;height:184px;background:var(--soft);border:1px solid #d9d9d9;padding:10px 14px;position:relative}
.comments h3{font-size:12.5px;font-weight:700;color:#333}
.comment{display:flex;gap:18px;padding:10px 0;border-bottom:1px solid #ddd;font-size:11.5px;line-height:18px;color:#555}
.comment:last-of-type{border-bottom:none}
.comment .avatar{flex:none;width:34px;height:34px;background:linear-gradient(160deg,#d6b79a,#6b4b36);border:2px solid #fff}
.comment-input{position:absolute;left:14px;right:14px;bottom:12px;height:30px;border:1px solid #ccc;background:#fff;font-size:11.5px;color:#aaa;font-style:italic;padding:7px 10px}

.load-more{position:absolute;left:100px;top:2678px;width:630px;height:40px;background:#ececec;display:flex;justify-content:center;align-items:center;gap:8px;font-size:12.5px;color:#333}

/* sidebar */
.sidebar{position:absolute;left:763px;top:0;width:335px}
.widget{position:absolute;left:0;width:335px;border:1px solid var(--line)}
.widget-head{height:40px;background:var(--panel);color:#fff;font-size:19px;display:flex;align-items:center;gap:10px;padding-left:18px}
.widget-head svg{width:20px;height:20px}
.search-field{margin:16px 18px;height:38px;border:1px solid #ddd;font-size:11.5px;color:#aaa;padding:11px 10px;position:relative}
.search-field svg{position:absolute;right:10px;top:11px;width:15px;height:15px}

.tabs{display:flex;height:42px}
.tabs span{flex:1;display:flex;align-items:center;justify-content:center;gap:8px;background:var(--panel);color:#fff;font-size:12.5px}
.tabs span.on{background:#fff;color:#222}
.tabs i{width:12px;height:12px;border-radius:50%;background:currentColor;display:block}
.feed-item{display:flex;gap:10px;padding:12px 10px 0}
.feed-item .avatar{flex:none;width:52px;height:50px;background:linear-gradient(160deg,#caa182,#4d3325)}
.feed-item p{font-size:10.5px;line-height:13px;color:#555;width:190px}
.like{display:inline-block;margin-top:3px;border:1px solid #c5cce0;background:#eef1f7;color:#3b4d7a;font-size:9.5px;padding:0 4px}

.archives ul{list-style:none;padding:6px 20px}
.archives li{height:35.5px;line-height:35px;border-bottom:1px solid #eee;font-size:13.5px;color:#444;padding-left:18px;position:relative}
.archives li:last-child{border-bottom:none}
.archives li::before{content:"";position:absolute;left:0;top:16px;width:4px;height:4px;border-radius:50%;background:var(--orange)}

.newsletter{padding:16px 14px}
.newsletter h4{font-size:19px;font-weight:400;color:#222}
.newsletter p{font-size:11.5px;color:#555;margin-top:10px}
.newsletter .email{margin-top:14px;height:34px;border:1px solid #ddd;font-size:11px;color:#999;font-style:italic;padding:9px 10px}
.newsletter .submit{margin-top:12px;width:90px;height:33px;background:var(--orange);color:#fff;font-size:14px;font-weight:700;text-align:center;line-height:33px}

.ad{position:absolute;left:0;width:335px}

.site-footer{position:absolute;left:0;top:2743px;width:1200px;height:43px;background:var(--panel);color:#eee;font-size:11.5px;text-align:center;line-height:43px}
.site-footer b{color:#fff}
</style>
</head>
<body>
<div class="page">
  <div class="topline"></div>

  <header class="site-header">
    <div class="brand">Tandem K</div>
    <nav class="main-nav">
      <a class="active" style="left:568px">About Me</a>
      <a style="left:683px">Recent Blog</a>
      <a style="left:823px">Reader Comments</a>
      <a style="left:1008px">Contact Us</a>
    </nav>
  </header>

  <section class="hero" role="img" aria-label="Photograph of a hiker with a backpack standing in a mountain valley">
    <div class="about-card">
      <h1>ABOUT ME</h1>
      <p>Lorem ipsum dolor sit amet, consectetur adipiscing elit. Sed vitae magna tellus. Aenean ante nunc, semper nec cursus non, rutrum ac eros. Vestibulum mattis justo ac dui bibendum consequat a ac ipsum. Praesent a arcu venenatis, auctor velit eu, suscipit libero.</p>
      <div class="more">+</div>
    </div>
  </section>

  <main class="posts">
    <article class="post first">
      <h2>Lorem ipsum dolor sit</h2>
      <div class="post-sub">Duis aute irure dolor in reprehenderit</div>
      <div class="post-body">
        <p>Lorem ipsum dolor sit amet, consecit adipiscing elit, sed do eiusmod tempor incidimen labore n dolorme laboris ni ut aliquip ex ena lin consequat Duis aute irure dolor in reprehenderit magna aliqua. Ut enim ad qnexercitation ullamco Neque porro quisquam est, qui dolorem ipsum quia dolor sit amet, conadipi velit sed quia non numquam eius modi tempora incidunt. ipsum quia dolor sit amet, conadipi velit sed quia non numquam eius modi tempora. <a>Read More</a></p>
        <div class="post-photo" role="img" aria-label="Portrait photo of a man in a jacket against a brick wall"></div>
      </div>
      <div class="post-meta">
        <span><svg viewBox="0 0 14 14"><path d="M1 3h12v10H1zM3 1h2v3H3zM9 1h2v3H9z"/></svg>02/06/2016</span>
        <span><svg viewBox="0 0 14 14"><path d="M7 2C3.5 2 1 4 1 6.5c0 1.4.8 2.6 2 3.4L2.5 13 6 11c.3 0 .7.1 1 .1 3.5 0 6-2 6-4.6S10.5 2 7 2z"/></svg>Leave A Comment</span>
        <span><svg viewBox="0 0 14 14"><path d="M1 6h3v7H1zM5 6l3-5c1 0 2 .6 1.6 2L9 5h3.5c.8 0 1.3.7 1.1 1.4l-1.4 5.6c-.2.6-.7 1-1.3 1H5z"/></svg>Like Us</span>
        <span><svg viewBox="0 0 14 14"><circle cx="11" cy="3" r="2"/><circle cx="3" cy="7" r="2"/><circle cx="11" cy="11" r="2"/><path d="M3 7l8-4M3 7l8 4" stroke="#f7a21b" stroke-width="1.3"/></svg>Share</span>
      </div>
      <div class="comments">
        <h3>Comments</h3>
        <div class="comment"><div class="avatar" role="img" aria-label="Reader avatar"></div><div>Lorem ipsum dolor sit amet, consecit adipiscing elit, sed do eiusmod tempor incidimen labore n dolorme laboris ni ut aliquip ex ena lin consequat Duis aute irure dolor in reprehenderit magna aliqua. Ut enim</div></div>
        <div class="comment"><div class="avatar" role="img" aria-label="Reader avatar"></div><div>Lorem ipsum dolor sit amet, consecit adipiscing elit, sed do eiusmod tempor incidimen labore n dolorme laboris ni ut aliquip ex ena lin consequat.</div></div>
        <div class="comment-input">Write Comment</div>
      </div>
    </article>

    <article class="post">
      <h2>Lorem ipsum dolor sit</h2>
      <div class="post-sub">Duis aute irure dolor in reprehenderit</div>
      <div class="post-body">
        <p>Lorem ipsum dolor sit amet, consecit adipiscing elit, sed do eiusmod tempor incidimen labore n dolorme laboris ni ut aliquip ex ena lin consequat Duis aute irure dolor in reprehenderit magna aliqua. Ut enim ad qnexercitation ullamco Neque porro quisquam est, qui dolorem ipsum quia dolor sit amet, conadipi velit sed quia non numquam eius modi tempora incidunt. ipsum quia dolor sit amet, conadipi velit sed quia non numquam eius modi tempora. <a>Read More</a></p>
        <div class="post-photo" style="background:linear-gradient(160deg,#e6d3b5,#8a6a55)" role="img" aria-label="Portrait photo of a blonde woman"></div>
      </div>
      <div class="post-meta">
        <span><svg viewBox="0 0 14 14"><path d="M1 3h12v10H1zM3 1h2v3H3zM9 1h2v3H9z"/></svg>02/06/2016</span>
        <span><svg viewBox="0 0 14 14"><path d="M7 2C3.5 2 1 4 1 6.5c0 1.4.8 2.6 2 3.4L2.5 13 6 11c.3 0 .7.1 1 .1 3.5 0 6-2 6-4.6S10.5 2 7 2z"/></svg>Leave A Comment</span>
        <span><svg viewBox="0 0 14 14"><path d="M1 6h3v7H1zM5 6l3-5c1 0 2 .6 1.6 2L9 5h3.5c.8 0 1.3.7 1.1 1.4l-1.4 5.6c-.2.6-.7 1-1.3 1H5z"/></svg>Like Us</span>
        <span><svg viewBox="0 0 14 14"><circle cx="11" cy="3" r="2"/><circle cx="3" cy="7" r="2"/><circle cx="11" cy="11" r="2"/><path d="M3 7l8-4M3 7l8 4" stroke="#f7a21b" stroke-width="1.3"/></svg>Share</span>
      </div>
    </article>

    <article class="post">
      <h2>Lorem ipsum dolor sit</h2>
      <div class="post-sub">Duis aute irure dolor in reprehenderit</div>
      <div class="post-body">
        <p>Lorem ipsum dolor sit amet, consecit adipiscing elit, sed do eiusmod tempor incidimen labore n dolorme laboris ni ut aliquip ex ena lin consequat Duis aute irure dolor in reprehenderit magna aliqua. Ut enim ad qnexercitation ullamco Neque porro quisquam est, qui dolorem ipsum quia dolor sit amet, conadipi velit sed quia non numquam eius modi tempora incidunt. ipsum quia dolor sit amet, conadipi velit sed quia non numquam eius modi tempora. <a>Read More</a></p>
        <div class="post-photo" style="background:linear-gradient(160deg,#b9d3d6,#7a6a5c)" role="img" aria-label="Portrait photo of a man in a shirt"></div>
      </div>
      <div class="post-meta">
        <span><svg viewBox="0 0 14 14"><path d="M1 3h12v10H1zM3 1h2v3H3zM9 1h2v3H9z"/></svg>02/06/2016</span>
        <span><svg viewBox="0 0 14 14"><path d="M7 2C3.5 2 1 4 1 6.5c0 1.4.8 2.6 2 3.4L2.5 13 6 11c.3 0 .7.1 1 .1 3.5 0 6-2 6-4.6S10.5 2 7 2z"/></svg>Leave A Comment</span>
        <span><svg viewBox="0 0 14 14"><path d="M1 6h3v7H1zM5 6l3-5c1 0 2 .6 1.6 2L9 5h3.5c.8 0 1.3.7 1.1 1.4l-1.4 5.6c-.2.6-.7 1-1.3 1H5z"/></svg>Like Us</span>
        <span><svg viewBox="0 0 14 14"><circle cx="11" cy="3" r="2"/><circle cx="3" cy="7" r="2"/><circle cx="11" cy="11" r="2"/><path d="M3 7l8-4M3 7l8 4" stroke="#f7a21b" stroke-width="1.3"/></svg>Share</span>
      </div>
    </article>

    <article class="post">
      <h2>Lorem ipsum dolor sit</h2>
      <div class="post-sub">Duis aute irure dolor in reprehenderit</div>
      <div class="post-body">
        <p>Lorem ipsum dolor sit amet, consecit adipiscing elit, sed do eiusmod tempor incidimen labore n dolorme laboris ni ut aliquip ex ena lin consequat Duis aute irure dolor in reprehenderit magna aliqua. Ut enim ad qnexercitation ullamco Neque porro quisquam est, qui dolorem ipsum quia dolor sit amet, conadipi velit sed quia non numquam eius modi tempora incidunt. ipsum quia dolor sit amet, conadipi velit sed quia non numquam eius modi tempora. <a>Read More</a></p>
        <div class="post-photo" style="background:linear-gradient(160deg,#9a9a9a,#2e2e2e)" role="img" aria-label="Black and white portrait photo of a man in a suit"></div>
      </div>
      <div class="post-meta">
        <span><svg viewBox="0 0 14 14"><path d="M1 3h12v10H1zM3 1h2v3H3zM9 1h2v3H9z"/></svg>02/06/2016</span>
        <span><svg viewBox="0 0 14 14"><path d="M7 2C3.5 2 1 4 1 6.5c0 1.4.8 2.6 2 3.4L2.5 13 6 11c.3 0 .7.1 1 .1 3.5 0 6-2 6-4.6S10.5 2 7 2z"/></svg>Leave A Comment</span>
        <span><svg viewBox="0 0 14 14"><path d="M1 6h3v7H1zM5 6l3-5c1 0 2 .6 1.6 2L9 5h3.5c.8 0 1.3.7 1.1 1.4l-1.4 5.6c-.2.6-.7 1-1.3 1H5z"/></svg>Like Us</span>
        <span><svg viewBox="0 0 14 14"><circle cx="11" cy="3" r="2"/><circle cx="3" cy="7" r="2"/><circle cx="11" cy="11" r="2"/><path d="M3 7l8-4M3 7l8 4" stroke="#f7a21b" stroke-width="1.3"/></svg>Share</span>
      </div>
    </article>

    <article class="post">
      <h2>Lorem ipsum dolor sit</h2>
      <div class="post-sub">Duis aute irure dolor in reprehenderit</div>
      <div class="post-body">
        <p>Lorem ipsum dolor sit amet, consecit adipiscing elit, sed do eiusmod tempor incidimen labore n dolorme laboris ni ut aliquip ex ena lin consequat Duis aute irure dolor in reprehenderit magna aliqua. Ut enim ad qnexercitation ullamco Neque porro quisquam est, qui dolorem ipsum quia dolor sit amet, conadipi velit sed quia non numquam eius modi tempora incidunt. ipsum quia dolor sit amet, conadipi velit sed quia non numquam eius modi tempora. <a>Read More</a></p>
        <div class="post-photo" style="background:linear-gradient(160deg,#eef0f2,#b6ab9c)" role="img" aria-label="Portrait photo of a woman in a white blouse in an office"></div>
      </div>
      <div class="post-meta">
        <span><svg viewBox="0 0 14 14"><path d="M1 3h12v10H1zM3 1h2v3H3zM9 1h2v3H9z"/></svg>02/06/2016</span>
        <span><svg viewBox="0 0 14 14"><path d="M7 2C3.5 2 1 4 1 6.5c0 1.4.8 2.6 2 3.4L2.5 13 6 11c.3 0 .7.1 1 .1 3.5 0 6-2 6-4.6S10.5 2 7 2z"/></svg>Leave A Comment</span>
        <span><svg viewBox="0 0 14 14"><path d="M1 6h3v7H1zM5 6l3-5c1 0 2 .6 1.6 2L9 5h3.5c.8 0 1.3.7 1.1 1.4l-1.4 5.6c-.2.6-.7 1-1.3 1H5z"/></svg>Like Us</span>
        <span><svg viewBox="0 0 14 14"><circle cx="11" cy="3" r="2"/><circle cx="3" cy="7" r="2"/><circle cx="11" cy="11" r="2"/><path d="M3 7l8-4M3 7l8 4" stroke="#f7a21b" stroke-width="1.3"/></svg>Share</span>
      </div>
    </article>

    <article class="post">
      <h2>Lorem ipsum dolor sit</h2>
      <div class="post-sub">Duis aute irure dolor in reprehenderit</div>
      <div class="post-body">
        <p>Lorem ipsum dolor sit amet, consecit adipiscing elit, sed do eiusmod tempor incidimen labore n dolorme laboris ni ut aliquip ex ena lin consequat Duis aute irure dolor in reprehenderit magna aliqua. Ut enim ad qnexercitation ullamco Neque porro quisquam est, qui dolorem ipsum quia dolor sit amet, conadipi velit sed quia non numquam eius modi tempora incidunt. ipsum quia dolor sit amet, conadipi velit sed quia non numquam eius modi tempora. <a>Read More</a></p>
        <div class="post-photo" style="background:linear-gradient(160deg,#d8d8d8,#3d3a3a)" role="img" aria-label="Portrait photo of a smiling woman in a dark blazer"></div>
      </div>
      <div class="post-meta">
        <span><svg viewBox="0 0 14 14"><path d="M1 3h12v10H1zM3 1h2v3H3zM9 1h2v3H9z"/></svg>02/06/2016</span>
        <span><svg viewBox="0 0 14 14"><path d="M7 2C3.5 2 1 4 1 6.5c0 1.4.8 2.6 2 3.4L2.5 13 6 11c.3 0 .7.1 1 .1 3.5 0 6-2 6-4.6S10.5 2 7 2z"/></svg>Leave A Comment</span>
        <span><svg viewBox="0 0 14 14"><path d="M1 6h3v7H1zM5 6l3-5c1 0 2 .6 1.6 2L9 5h3.5c.8 0 1.3.7 1.1 1.4l-1.4 5.6c-.2.6-.7 1-1.3 1H5z"/></svg>Like Us</span>
        <span><svg viewBox="0 0 14 14"><circle cx="11" cy="3" r="2"/><circle cx="3" cy="7" r="2"/><circle cx="11" cy="11" r="2"/><path d="M3 7l8-4M3 7l8 4" stroke="#f7a21b" stroke-width="1.3"/></svg>Share</span>
      </div>
    </article>

    <article class="post last">
      <h2>Lorem ipsum dolor sit</h2>
      <div class="post-sub">Duis aute irure dolor in reprehenderit</div>
      <div class="post-body">
        <p>Lorem ipsum dolor sit amet, consecit adipiscing elit, sed do eiusmod tempor incidimen labore n dolorme laboris ni ut aliquip ex ena lin consequat Duis aute irure dolor in reprehenderit magna aliqua. Ut enim ad qnexercitation ullamco Neque porro quisquam est, qui dolorem ipsum quia dolor sit amet, conadipi velit sed quia non numquam eius modi tempora incidunt. ipsum quia dolor sit amet, conadipi velit sed quia non numquam eius modi tempora. <a>Read More</a></p>
        <div class="post-photo" style="background:linear-gradient(160deg,#f4f4f4,#6a4e3e)" role="img" aria-label="Portrait photo of a young man in a dark sweater"></div>
      </div>
      <div class="post-meta">
        <span><svg viewBox="0 0 14 14"><path d="M1 3h12v10H1zM3 1h2v3H3zM9 1h2v3H9z"/></svg>02/06/2016</span>
        <span><svg viewBox="0 0 14 14"><path d="M7 2C3.5 2 1 4 1 6.5c0 1.4.8 2.6 2 3.4L2.5 13 6 11c.3 0 .7.1 1 .1 3.5 0 6-2 6-4.6S10.5 2 7 2z"/></svg>Leave A Comment</span>
        <span><svg viewBox="0 0 14 14"><path d="M1 6h3v7H1zM5 6l3-5c1 0 2 .6 1.6 2L9 5h3.5c.8 0 1.3.7 1.1 1.4l-1.4 5.6c-.2.6-.7 1-1.3 1H5z"/></svg>Like Us</span>
        <span><svg viewBox="0 0 14 14"><circle cx="11" cy="3" r="2"/><circle cx="3" cy="7" r="2"/><circle cx="11" cy="11" r="2"/><path d="M3 7l8-4M3 7l8 4" stroke="#f7a21b" stroke-width="1.3"/></svg>Share</span>
      </div>
    </article>
  </main>

  <div class="load-more">
    <svg width="18" height="18" viewBox="0 0 18 18" fill="none" stroke="#888" stroke-width="2" stroke-linecap="round"><path d="M9 1v4M9 13v4M1 9h4M13 9h4M3.3 3.3l2.8 2.8M11.9 11.9l2.8 2.8M3.3 14.7l2.8-2.8M11.9 6.1l2.8-2.8"/></svg>
    Load More Blog
  </div>

  <aside class="sidebar">
    <section class="widget" style="top:539px;height:111px">
      <div class="widget-head">
        <svg viewBox="0 0 20 20" fill="none" stroke="#fff" stroke-width="2.2"><circle cx="4" cy="16" r="1.8" fill="#fff" stroke="none"/><path d="M3 9a8 8 0 0 1 8 8M3 3a14 14 0 0 1 14 14"/></svg>
        Search Blog
      </div>
      <div class="search-field">Search...
        <svg viewBox="0 0 16 16" fill="none" stroke="#bbb" stroke-width="2"><circle cx="6.5" cy="6.5" r="5"/><path d="M10.5 10.5L15 15"/></svg>
      </div>
    </section>

    <section class="widget" style="top:680px;height:334px">
      <div class="tabs">
        <span class="on"><i></i>Friendwall</span>
        <span><i></i>Chirper</span>
        <span><i></i>Picturely</span>
      </div>
      <div class="feed-item"><div class="avatar" role="img" aria-label="Follower photo"></div><p>Lorem Ipsum is simply dummy text of the. printing and typesetting...<br><span class="like">Like</span></p></div>
      <div class="feed-item"><div class="avatar" role="img" aria-label="Follower photo"></div><p>Lorem Ipsum is simply dummy text of the. printing and typesetting...<br><span class="like">Like</span></p></div>
      <div class="feed-item"><div class="avatar" role="img" aria-label="Follower photo"></div><p>Lorem Ipsum is simply dummy text of the. printing and typesetting...<br><span class="like">Like</span></p></div>
      <div class="feed-item"><div class="avatar" role="img" aria-label="Follower photo"></div><p>Lorem Ipsum is simply dummy text of the. printing and typesetting...<br><span class="like">Like</span></p></div>
    </section>

    <section class="widget archives" style="top:1046px;height:232px">
      <div class="widget-head">
        <svg viewBox="0 0 20 20" fill="none" stroke="#fff" stroke-width="1.8"><path d="M4 1h8l4 4v14H4zM12 1v4h4M7 10h6M7 14h6"/></svg>
        Archives
      </div>
      <ul>
        <li>July 2016</li>
        <li>June 2016</li>
        <li>May 2016</li>
        <li>April 2016</li>
        <li>February 2016</li>
      </ul>
    </section>

    <section class="widget newsletter" style="top:1309px;height:164px">
      <h4>SignUp For Newsletter</h4>
      <p>Lorem ipsum dolor sit amet, consecit</p>
      <div class="email">Enter your email address</div>
      <div class="submit">SUBMIT</div>
    </section>

    <div class="ad" style="top:1506px;height:251px;background:#8f8f8f" role="img" aria-label="Grey promotional poster with a bold quote"></div>
    <div class="ad" style="top:1790px;height:192px;background:linear-gradient(120deg,#c79a6a,#a9784f)" role="img" aria-label="Illustration of striped legs in red sneakers on a tan dotted background"></div>
  </aside>

  <footer class="site-footer">Copyright © 2016 <b>Tandem K</b>. All Rights Reserved.</footer>
</div>
</body>
</html>
```